Quote Cards With KB May 2025 for Instagram

I would like to put these quotes over one of the pictures attached; Instagram (new size: 4:5 (1080 x 1350 pixels) One Quote per picture, and I want the quote to be bold or easy to read as well. I provided a few reference graphics that I really like as examples below. In very small letters at the bottom add @KBHarlowOnline

All of the pictures are attached; you can pick any photo and add one quote to it; but no stock photography

```html
<!DOCTYPE html>
<html lang="en">
<head>
<meta charset="UTF-8">
<title>Quote Card — KB</title>
<link href="https://fonts.googleapis.com/css2?family=Bebas+Neue&display=swap" rel="stylesheet">
<style>
  :root {
    --bg-dark: #1b1b1b;
    --bg-mid: #2a2a2a;
    --ink: #ffffff;
    --accent: #d9484a;
    --handle-ghost: rgba(120, 120, 120, 0.55);
    --photo-light: #8a8a8a;
    --photo-dark: #2c2c2c;
  }
  * { margin: 0; padding: 0; box-sizing: border-box; }
  html, body {
    width: 960px;
    height: 1200px;
    overflow: hidden;
    background: var(--bg-dark);
  }
  .quote-card {
    position: relative;
    width: 960px;
    height: 1200px;
    overflow: hidden;
    background:
      radial-gradient(ellipse at 55% 35%, var(--bg-mid) 0%, var(--bg-dark) 70%);
    font-family: "Bebas Neue", "Oswald", sans-serif;
  }
  .ghost-handle {
    position: absolute;
    left: 572px;
    top: 78px;
    writing-mode: vertical-rl;
    font-size: 168px;
    line-height: 1;
    letter-spacing: -2px;
    color: var(--handle-ghost);
    white-space: nowrap;
  }
  .portrait {
    position: absolute;
    left: 215px;
    top: 100px;
    width: 665px;
    height: 1100px;
    border-radius: 330px 330px 0 0;
    background:
      radial-gradient(ellipse at 50% 22%, var(--photo-light) 0%, #4a4a4a 30%, var(--photo-dark) 65%, transparent 85%);
    opacity: 0.85;
  }
  .quote-mark {
    position: absolute;
    left: 124px;
    top: 658px;
    width: 60px;
    height: 44px;
  }
  .quote-text {
    position: absolute;
    left: 124px;
    top: 736px;
    color: var(--ink);
    font-size: 55px;
    line-height: 67px;
    letter-spacing: -0.5px;
    text-transform: uppercase;
  }
  .handle {
    position: absolute;
    left: 124px;
    top: 1042px;
    color: var(--ink);
    font-size: 31px;
    letter-spacing: -0.3px;
  }
</style>
</head>
<body>
  <main class="quote-card">
    <div class="ghost-handle">@KBHARLOWONLINE</div>
    <div class="portrait" role="img" aria-label="Black and white portrait of KB smiling, wearing a black long-sleeve top, hand on hip"></div>

    <svg class="quote-mark" viewBox="0 0 60 44" aria-hidden="true">
      <path fill="var(--accent)" d="M0 44 V22 C0 9 7 2 19 0 L21 6 C14 8 11 12 11 18 H26 V44 Z"/>
      <path fill="var(--accent)" d="M34 44 V22 C34 9 41 2 53 0 L55 6 C48 8 45 12 45 18 H60 V44 Z"/>
    </svg>

    <p class="quote-text">
      What worked in<br>
      your 30s won’t work now.<br>
      Here’s what actually does.<br>
      Drop 30 pounds in 3 months.
    </p>

    <p class="handle">@KBHARLOWONLINE</p>
  </main>
</body>
</html>
```